Business Card Design Project

Business Card
We are rebranding with a new logo
Industry/Entity Type
Business
Contact Information for Business Card
Dennis Morvale +61 487215963 dennis@quorv.com.au P.O. Box 872 Fernlow QLD 4309
Requirements
Must have
- Logo

```html
<!DOCTYPE html>
<html lang="en">
<head>
<meta charset="utf-8">
<title>Quorv International – Business Card</title>
<link rel="stylesheet" href="https://fonts.googleapis.com/css2?family=Open+Sans:wght@400;600;700&display=swap">
<style>
  :root {
    --bg: #3a3c40;
    --blue: #0f6f96;
    --blue-deep: #0a4f70;
    --blue-light: #2a9cc6;
    --name-blue: #1a8fc4;
    --orange: #e87a1e;
    --paper: #f6f6f4;
    --ink: #4a4a4a;
    --rule: #9a9a9a;
  }
  * { margin: 0; padding: 0; box-sizing: border-box; }
  html, body { width: 1200px; height: 960px; overflow: hidden; }
  body {
    background: var(--bg);
    font-family: "Open Sans", Arial, sans-serif;
    display: flex;
    flex-direction: column;
    align-items: center;
    justify-content: center;
    gap: 46px;
  }
  .card {
    position: relative;
    width: 740px;
    height: 411px;
    overflow: hidden;
  }

  /* Back side */
  .card-back {
    background: radial-gradient(ellipse at 50% 40%, var(--blue-light) 0%, var(--blue) 55%, var(--blue-deep) 100%);
    color: #fff;
    display: flex;
    flex-direction: column;
    align-items: center;
    justify-content: center;
  }
  .card-back .brand {
    font-size: 58px;
    font-weight: 600;
    letter-spacing: 1px;
    color: #fff;
  }
  .card-back .web {
    margin-top: 40px;
    font-size: 17px;
    letter-spacing: 6px;
    color: rgba(255,255,255,0.85);
  }

  /* Front side */
  .card-front { background: var(--paper); }
  .card-front .edge {
    position: absolute;
    inset: 0;
  }
  .card-front .brand {
    position: absolute;
    left: 70px;
    top: 52px;
    font-size: 34px;
    font-weight: 600;
    color: var(--blue);
    line-height: 1.1;
  }
  .card-front .person {
    position: absolute;
    left: 70px;
    top: 176px;
    font-size: 17px;
    font-weight: 700;
    color: var(--name-blue);
    text-transform: uppercase;
    letter-spacing: 0.3px;
  }
  .contact-list {
    position: absolute;
    left: 70px;
    top: 214px;
    list-style: none;
    font-size: 15px;
    color: var(--ink);
    line-height: 22px;
  }
  .contact-list li { display: flex; align-items: center; gap: 10px; }
  .contact-list svg { width: 13px; height: 13px; fill: var(--name-blue); flex: none; }
  .card-front .rule {
    position: absolute;
    left: 70px;
    top: 300px;
    width: 520px;
    height: 1px;
    background: var(--rule);
  }
  .card-front .address {
    position: absolute;
    right: 150px;
    top: 322px;
    text-align: right;
    font-size: 16px;
    line-height: 21px;
    color: var(--ink);
  }
</style>
</head>
<body>

  <section class="card card-back" aria-label="Business card back">
    <div class="brand">Quorv International</div>
    <div class="web">www.quorv.com.au</div>
  </section>

  <section class="card card-front" aria-label="Business card front">
    <svg class="edge" viewBox="0 0 740 411" preserveAspectRatio="none" aria-hidden="true">
      <defs>
        <linearGradient id="bandFill" x1="0" y1="0" x2="1" y2="1">
          <stop offset="0" stop-color="#1680a8"/>
          <stop offset="1" stop-color="#0a4f70"/>
        </linearGradient>
      </defs>
      <path d="M470 0 Q690 120 706 411 L740 411 L740 0 Z" fill="url(#bandFill)"/>
      <path d="M470 0 Q682 124 690 411" fill="none" stroke="#ffffff" stroke-width="9"/>
      <path d="M466 0 Q672 126 680 411" fill="none" stroke="var(--orange)" stroke-width="6"/>
    </svg>

    <div class="brand">Quorv International</div>
    <div class="person">Dennis Morvale</div>
    <ul class="contact-list">
      <li>
        <svg viewBox="0 0 16 16"><path d="M3 1l3 3-1.5 2a9 9 0 0 0 5.5 5.5L12 10l3 3-2 2C7 15 1 9 1 3z"/></svg>
        +61 487215963
      </li>
      <li>
        <svg viewBox="0 0 16 16"><path d="M1 3h14v10H1z M1 3l7 6 7-6" stroke="#fff" stroke-width="1"/></svg>
        dennis@quorv.com.au
      </li>
      <li>
        <svg viewBox="0 0 16 16"><circle cx="8" cy="8" r="7"/></svg>
        www.quorv.com.au
      </li>
    </ul>
    <div class="rule"></div>
    <div class="address">P.O. Box 872<br>Fernlow QLD 4309</div>
  </section>

</body>
</html>
```